Business card for my new company (Accounting firm)

I need a business card for my new business Brightwell Advisory and Ledger SA. Our services are accounting, tax, audit and financial management. Our customers are small companies, start-ups and new companies. The final design has to show financial security, trust and growth. Please find our logo attached to the business card. Text for the business card: Brightwell Advisory and Ledger SA Tomas Varenholt Director and Founder Certified Accountant Tel. 022 418 57 34 tv@clairevalconseil.ch www.clairevalconseil.ch Rue des Vergières 27 1201 Geneva
Target Market(s)
Our customers are small companies, start-ups and new companies.
Industry/Entity Type
Finance And Accounting
Contact Information for Business Card
Claireval Conseil et Comptes SA
Tomas Varenholt
Directeur et Fondateur
Expert-comptable diplômé
Tél. 022 418 57 34
tv@clairevalconseil.ch
www.clairevalconseil.ch
Rue des Vergières 27
1201 Genève

```html
<!DOCTYPE html>
<html lang="fr">
<head>
<meta charset="utf-8">
<title>Claireval Conseil et Comptes SA – Carte de visite</title>
<link rel="stylesheet" href="https://fonts.googleapis.com/css2?family=Roboto:wght@400;500;700&display=swap">
<style>
  :root {
    --stage: #e4e5e7;
    --blue-light: #2b9fd6;
    --blue-deep: #1c6ea6;
    --blue-name: #1f5f99;
    --ink: #3a3d42;
    --ink-soft: #55595f;
    --paper: #f7f7f7;
    --white: #ffffff;
  }
  * { box-sizing: border-box; margin: 0; padding: 0; }
  html, body { width: 1200px; height: 726px; overflow: hidden; }
  body {
    background: var(--stage);
    font-family: "Roboto", Arial, sans-serif;
    position: relative;
  }
  .card {
    position: absolute;
    top: 203px;
    width: 520px;
    height: 320px;
    border-radius: 4px;
    box-shadow: 0 10px 24px rgba(0,0,0,0.14);
    overflow: hidden;
  }
  /* Front */
  .card-front {
    left: 80px;
    background: linear-gradient(135deg, var(--blue-light) 0%, var(--blue-deep) 100%);
    color: var(--white);
    display: flex;
    flex-direction: column;
    align-items: center;
    justify-content: center;
    text-align: center;
  }
  .front-mark {
    display: flex;
    align-items: center;
    gap: 12px;
  }
  .front-mark .dot {
    width: 18px; height: 18px;
    background: var(--white);
  }
  .brand-name {
    font-weight: 500;
    letter-spacing: 1px;
  }
  .card-front .brand-name { font-size: 28px; color: var(--white); }
  .front-web {
    margin-top: 30px;
    font-size: 15px;
    font-weight: 700;
    letter-spacing: 0.3px;
  }
  /* Back */
  .card-back {
    left: 620px;
    background: var(--paper);
  }
  .back-band {
    position: absolute;
    left: 0; right: 0; bottom: 0;
    height: 10px;
    background: linear-gradient(90deg, var(--blue-light), var(--blue-deep));
  }
  .back-brand {
    position: absolute;
    top: 34px; right: 30px;
    text-align: right;
  }
  .back-brand .brand-name {
    font-size: 19px;
    color: var(--blue-name);
    display: flex;
    align-items: center;
    justify-content: flex-end;
    gap: 8px;
  }
  .back-brand .square {
    width: 12px; height: 12px;
    background: var(--blue-name);
  }
  .back-brand .web {
    margin-top: 8px;
    font-size: 12px;
    color: var(--ink);
  }
  .person {
    position: absolute;
    left: 30px; top: 150px;
  }
  .person-name {
    font-size: 21px;
    font-weight: 700;
    color: var(--blue-name);
  }
  .person-role {
    margin-top: 4px;
    font-size: 12px;
    line-height: 1.35;
    color: var(--ink-soft);
  }
  .contacts {
    position: absolute;
    left: 30px; top: 236px;
    font-size: 12.5px;
    color: var(--ink);
    list-style: none;
  }
  .contacts li {
    display: flex;
    align-items: center;
    gap: 14px;
    margin-bottom: 8px;
  }
  .contact-item {
    display: inline-flex;
    align-items: center;
    gap: 6px;
  }
  .icon { width: 13px; height: 13px; fill: var(--blue-name); flex: none; }
</style>
</head>
<body>

<section class="card card-front" aria-label="Recto de la carte">
  <div class="front-mark">
    <span class="dot"></span>
    <span class="brand-name">Claireval Conseil et Comptes</span>
  </div>
  <p class="front-web">www.clairevalconseil.ch</p>
</section>

<section class="card card-back" aria-label="Verso de la carte">
  <div class="back-brand">
    <div class="brand-name"><span class="square"></span>Claireval Conseil et Comptes</div>
    <div class="web">www.clairevalconseil.ch</div>
  </div>

  <div class="person">
    <h1 class="person-name">Tomas Varenholt</h1>
    <p class="person-role">Directeur et Fondateur<br>Expert-comptable diplômé</p>
  </div>

  <ul class="contacts">
    <li>
      <span class="contact-item">
        <svg class="icon" viewBox="0 0 16 16"><path d="M3.5 1.5l2.5 0 1.2 3.2-1.6 1.2a8 8 0 0 0 4.5 4.5l1.2-1.6 3.2 1.2v2.5c0 .8-.7 1.5-1.5 1.5A12 12 0 0 1 2 3c0-.8.7-1.5 1.5-1.5z"/></svg>
        022 418 57 34
      </span>
      <span class="contact-item">
        <svg class="icon" viewBox="0 0 16 16"><path d="M1 3h14v10H1z M1.5 3.5L8 9l6.5-5.5" fill="var(--blue-name)"/><path d="M1.8 3.8L8 8.8l6.2-5" fill="none" stroke="#f7f7f7" stroke-width="1.2"/></svg>
        tv@clairevalconseil.ch
      </span>
      <span class="contact-item">
        <svg class="icon" viewBox="0 0 16 16"><circle cx="8" cy="8" r="7"/><path d="M1 8h14M8 1c-3 3.5-3 10.5 0 14M8 1c3 3.5 3 10.5 0 14" fill="none" stroke="#f7f7f7" stroke-width="1"/></svg>
        www.clairevalconseil.ch
      </span>
    </li>
    <li>
      <span class="contact-item">
        <svg class="icon" viewBox="0 0 16 16"><path d="M8 0.5a5 5 0 0 0-5 5c0 4 5 10 5 10s5-6 5-10a5 5 0 0 0-5-5zm0 7a2 2 0 1 1 0-4 2 2 0 0 1 0 4z"/></svg>
        Rue des Vergières 27 1201 Genève
      </span>
    </li>
  </ul>

  <div class="back-band"></div>
</section>

</body>
</html>
```